Family-owned company selling organic landscaping and gardening products needs new labels.

We need label designs initially for 6 products, the designs should be unique for each product but have common design elements. The products are organic and used in landscaping, gardening and horticulture industries. Products are used commercially and residentially. The products encourage root growth and soil health, so that could be featured in the label along with plants, trees, etc. We like the colors, the sunburst background and the art deco vibe in the label designs provided for inspiration, but we are open to other ideas as well. We are also providing a sample of current labels (bland, boring) for reference. We are also providing a copy of our new logo which we like but are open to suggestions. We would like to start with the label for our TERRA BLEND product.

```html
<!DOCTYPE html>
<html lang="en">
<head>
<meta charset="utf-8">
<title>Terra Blend Label – Front and Back</title>
<link rel="stylesheet" href="https://fonts.googleapis.com/css2?family=Anton&family=Antonio:wght@400;700&family=Montserrat:wght@500;700;800&family=Oswald:wght@700&display=swap">
<style>
  :root {
    --frame-brown: #a86a12;
    --title-brown: #7a4a0e;
    --sun-deep: #ebb512;
    --sun-mid: #f3c91f;
    --sun-light: #f8dc40;
    --sun-glow: #fff6a8;
    --leaf-dark: #1b6414;
    --leaf-mid: #2f8a22;
    --leaf-light: #5bb034;
    --badge-green: #0f6b2a;
    --ink: #111;
    --white: #fff;
  }
  * { box-sizing: border-box; margin: 0; padding: 0; }
  html, body { width: 1200px; height: 816px; overflow: hidden; background: var(--white); }
  .canvas { position: relative; width: 1200px; height: 816px; background: var(--white); }

  .label { position: absolute; }
  .label--front { left: 67px; top: 34px; width: 508px; height: 714px; }
  .label--back { left: 629px; top: 26px; width: 513px; height: 722px; }
  .label__frame { position: absolute; inset: 0; width: 100%; height: 100%; }

  .panel {
    position: absolute; left: 26px; top: 26px; overflow: hidden;
    background: radial-gradient(ellipse at 50% 52%, var(--sun-glow) 0%, var(--sun-light) 30%, var(--sun-mid) 62%, var(--sun-deep) 100%);
  }
  .label--front .panel {
    width: 456px; height: 662px;
    clip-path: path("M40,0 H416 A40,40 0 0 0 456,40 V622 A40,40 0 0 0 416,662 H40 A40,40 0 0 0 0,622 V40 A40,40 0 0 0 40,0 Z");
  }
  .label--back .panel {
    width: 461px; height: 670px;
    clip-path: path("M40,0 H421 A40,40 0 0 0 461,40 V630 A40,40 0 0 0 421,670 H40 A40,40 0 0 0 0,630 V40 A40,40 0 0 0 40,0 Z");
  }

  .brand-badge {
    position: absolute; border-radius: 50%; background: var(--white);
    border: 7px solid var(--frame-brown);
    display: flex; align-items: center; justify-content: center; text-align: center;
    font-family: "Montserrat", sans-serif; font-weight: 700; color: var(--title-brown);
    line-height: 1;
  }
  .label--front .brand-badge { left: 146px; top: 15px; width: 166px; height: 166px; font-size: 34px; }
  .label--back .brand-badge { left: 159px; top: 16px; width: 144px; height: 144px; font-size: 29px; }

  .product-title {
    position: absolute; left: 0; right: 0; top: 196px; text-align: center;
    font-family: "Anton", sans-serif; font-size: 74px; line-height: 1; letter-spacing: 1px;
    color: var(--title-brown);
    text-shadow: 3px 2px 0 var(--sun-light), 5px 4px 0 var(--frame-brown);
  }
  .product-subtitle {
    position: absolute; left: 0; right: 0; top: 294px; text-align: center;
    font-family: "Montserrat", sans-serif; font-weight: 500; font-size: 17px; color: var(--ink);
  }
  .product-tagline {
    position: absolute; left: 0; right: 0; top: 318px; text-align: center;
    font-family: "Montserrat", sans-serif; font-weight: 800; font-size: 17px; color: var(--ink);
  }

  .landscape-art {
    position: absolute; left: 0; top: 346px; width: 100%; height: 316px;
    background: linear-gradient(to bottom, rgba(47,138,34,0) 0%, var(--leaf-mid) 8%, var(--leaf-dark) 40%, var(--leaf-light) 54%, var(--leaf-mid) 74%, var(--leaf-dark) 100%);
  }
  .front-claim {
    position: absolute; left: 0; right: 0; text-align: center; color: var(--white);
    font-family: "Antonio", sans-serif; font-weight: 700; font-size: 17px; line-height: 1;
  }
  .front-claim--one { top: 593px; }
  .front-claim--two { top: 614px; }
  .front-weight {
    position: absolute; left: 0; right: 0; top: 642px; text-align: center; color: var(--white);
    font-family: "Antonio", sans-serif; font-weight: 400; font-size: 11.5px;
  }

  .back-copy {
    position: absolute; left: 0; right: 0; text-align: center; white-space: nowrap;
    font-family: "Antonio", sans-serif; font-weight: 400; font-size: 11.5px; line-height: 13.5px; color: var(--ink);
  }
  .back-copy h2 { font-size: 12px; font-weight: 700; line-height: 14px; }
  .back-copy--intro { top: 186px; }
  .back-copy--benefits { top: 241px; }
  .back-copy--claims { top: 324px; }
  .back-copy--ingredients { top: 410px; }
  .back-copy--application { top: 517px; }
  .back-weight {
    position: absolute; left: 0; right: 0; top: 642px; text-align: center;
    font-family: "Antonio", sans-serif; font-weight: 700; font-size: 16px; color: var(--ink);
  }

  .info-disc {
    position: absolute; top: 510px; width: 116px; height: 116px; border-radius: 50%;
    background: var(--badge-green); color: var(--white); white-space: nowrap;
    display: flex; flex-direction: column; align-items: center; justify-content: center;
    text-align: center; font-family: "Antonio", sans-serif; font-size: 8.5px; line-height: 10.5px;
  }
  .info-disc--caution { left: 13px; font-weight: 700; }
  .info-disc--maker { left: 332px; font-weight: 400; }
  .info-disc strong { font-weight: 700; }

  .side-caption {
    position: absolute; top: 760px; width: 200px; text-align: center;
    font-family: "Oswald", sans-serif; font-weight: 700; font-size: 27px; color: var(--ink);
  }
  .side-caption--front { left: 216px; }
  .side-caption--back { left: 787px; }
</style>
</head>
<body>
<main class="canvas">

  <section class="label label--front">
    <svg class="label__frame" viewBox="0 0 508 714" aria-hidden="true">
      <path d="M62,0 H446 A62,62 0 0 0 508,62 V652 A62,62 0 0 0 446,714 H62 A62,62 0 0 0 0,652 V62 A62,62 0 0 0 62,0 Z" fill="var(--frame-brown)"/>
      <path d="M66,8 H442 A58,58 0 0 0 500,66 V648 A58,58 0 0 0 442,706 H66 A58,58 0 0 0 8,648 V66 A58,58 0 0 0 66,8 Z" fill="none" stroke="var(--white)" stroke-width="2.5"/>
    </svg>
    <div class="panel">
      <div class="brand-badge">Loam<br>Field</div>
      <h1 class="product-title">TERRA BLEND</h1>
      <p class="product-subtitle">Endo-Ecto Mycorrhizal Inoculum</p>
      <p class="product-tagline">FOR MOST PLANTS</p>
      <div class="landscape-art" role="img" aria-label="Illustration of a forest of pine and broadleaf trees above rolling green striped hills"></div>
      <p class="front-claim front-claim--one">AUXILIARY SOIL AND PLANT SUBSTANCE</p>
      <p class="front-claim front-claim--two">NON PLANT FOOD INGREDIENT</p>
      <p class="front-weight">Net Weight: 1 lbs (453 grams)</p>
    </div>
  </section>

  <section class="label label--back">
    <svg class="label__frame" viewBox="0 0 513 722" aria-hidden="true">
      <path d="M62,0 H451 A62,62 0 0 0 513,62 V660 A62,62 0 0 0 451,722 H62 A62,62 0 0 0 0,660 V62 A62,62 0 0 0 62,0 Z" fill="var(--frame-brown)"/>
      <path d="M66,8 H447 A58,58 0 0 0 505,66 V656 A58,58 0 0 0 447,714 H66 A58,58 0 0 0 8,656 V66 A58,58 0 0 0 66,8 Z" fill="none" stroke="var(--white)" stroke-width="2.5"/>
    </svg>
    <div class="panel">
      <div class="brand-badge">Loam<br>Field</div>

      <div class="back-copy back-copy--intro">
        <p>DUAL-ROOT Paks contain both endo (arbuscular) mycorrhizal inoculum and ectomycorrhizal inoculum. Both<br>mycorrhizal groups are known to increase nutrient and water availability to colonized plants. Best results<br>occur after soils have been fumigated or severely disturbed.</p>
      </div>

      <div class="back-copy back-copy--benefits">
        <h2>BENEFITS</h2>
        <p>• All Natural - Non Toxic</p>
        <p>• Reduces Drought Stress; Water &amp; Fertilizer needs</p>
        <p>• Increases Plant Quality &amp; Yield; Water &amp; Nutrient Storage &amp; Uptake</p>
        <p>• Promotes extensive root system and soil structure, Plant establishment</p>
      </div>

      <div class="back-copy back-copy--claims">
        <h2>STATEMENT OF CLAIMS</h2>
        <p>Verdant Roots, LLC certifies that both endo/arbuscular Mycorrhizae and ecto<br>Mycorrhizae are present at the rates claimed on this label. Mycorrhizal symbiosis is sensitive<br>to environmental conditions and Verdant Roots is unable to guarantee the product beyond<br>this statement.</p>
      </div>

      <div class="back-copy back-copy--ingredients">
        <h2>ACTIVE INGREDIENTS</h2>
        <p>Contains eleven species of mycorrhizal fungi Mycorrhizal species and concentration: Glomus<br>intraradices, G. mosseae, G. aggregatum, G. etunicatum: 33 propagules/gm each Rhizopogon<br>villosullus, R. luteolus, R. amylopogon, R. fulvigleba: 5500 propagules/gm each Pisolithus<br>tinctorius: 200,000 propagules/gm Scleroderma cepa, S. citrinum:<br>11,000 propagules/gm each</p>
      </div>

      <div class="back-copy back-copy--application">
        <h2>APPLICATION RATES</h2>
        <p>Place the DUAL-ROOT Pak at the base<br>of the planting hole. Assure direct contact<br>occurs with the roots or root ball.<br>1 DUAL-ROOT Pak per plant up to 1 foot<br>(30 cm) of height. Add DUAL-ROOT Pak<br>to the planting hole at equal spacing for each<br>additional foot (30 cm) of height or width.</p>
      </div>

      <div class="info-disc info-disc--caution">
        <strong>CAUTION:</strong>
        <span>Do not swallow. Keep out</span>
        <span>of the reach of children</span>
        <span>and animals.</span>
        <span>Store in cool, dry place.</span>
      </div>

      <div class="info-disc info-disc--maker">
        <strong>Manufactured by:</strong>
        <span>Verdant Roots, LLC</span>
        <span>www.verdantrootsco.com</span>
        <span>P.O. Box 2480 • Oakdale, CA 95361</span>
        <span>Tel: 800-555-0142 /</span>
        <span>909-555-0187</span>
      </div>

      <p class="back-weight">Net Weight: 1 lbs (453 grams)</p>
    </div>
  </section>

  <p class="side-caption side-caption--front">Front</p>
  <p class="side-caption side-caption--back">Back</p>

</main>
</body>
</html>
```